Law Firm Business Card

This is a business card for a law firm that serves US military and veterans.

The card must have ONLY the following (we want an uncluttered look):

- Company logo (PNG, GIF, JPEG copies uploaded)
- A tagline reading: "a law firm for service members and veterans"
- My name and title: "Tobias Marlow" and "Attorney"
- My email: "tobias.marlow@brinmoorlegal.com"
- My number: "855-FIRM-ONE (347-6663)"

We are looking for a clean, simple layout with only the above information, likely printed on a bright white cotton stock. The font of our logo is DIN 1451, and the font used on our website is Helvetica Neue. The color of our logo is #336699, and we probably want the tagline in that color also, and my contact information in a dark grey. Please review our website at www.brinmoorlegal.com to ensure your card design complements our website style.

Thanks and we look forward to seeing your submissions.

A few notes:

- Two-sided submissions are ok
- Please don't add graphics (scales of justice, judges hammer, etc)

```html
<!DOCTYPE html>
<html lang="en">
<head>
<meta charset="utf-8">
<title>Brinmoor Legal – Business Card</title>
<link rel="stylesheet" href="https://fonts.googleapis.com/css2?family=Barlow+Semi+Condensed:wght@500;700&family=Barlow:wght@500;600&family=PT+Serif:ital@0;1&display=swap">
<style>
  :root {
    --brand-blue: #2b68c9;
    --tint-blue: #e8edf6;
    --ink: #1e1e1e;
    --paper: #ffffff;
    --backdrop: #ececec;
  }
  * { box-sizing: border-box; margin: 0; padding: 0; }
  html, body { width: 1200px; height: 526px; overflow: hidden; }
  body {
    background: var(--backdrop);
    position: relative;
    font-family: "Barlow", Helvetica, Arial, sans-serif;
  }
  .card {
    position: absolute;
    top: 113px;
    width: 525px;
    height: 300px;
    overflow: hidden;
  }
  .card--front { left: 45px; background: var(--paper); border: 1px solid #d4d4d4; }
  .card--back  { left: 630px; background: var(--brand-blue); }

  .wordmark {
    position: absolute;
    left: 30px;
    top: 28px;
    font-family: "Barlow Semi Condensed", "Arial Narrow", sans-serif;
    font-weight: 700;
    font-size: 42px;
    line-height: 40px;
    letter-spacing: 0.5px;
    color: var(--brand-blue);
    text-transform: uppercase;
  }
  .brand-block {
    position: absolute;
    left: 370px;
    top: 70px;
    width: 130px;
    height: 130px;
    background: var(--tint-blue);
  }
  .person {
    position: absolute;
    left: 30px;
    top: 165px;
    font-size: 17px;
    font-weight: 600;
    color: var(--brand-blue);
  }
  .person .title { font-size: 13px; font-weight: 600; color: var(--ink); }
  .contact {
    position: absolute;
    left: 30px;
    top: 196px;
    list-style: none;
    font-size: 13px;
    font-weight: 500;
    color: var(--ink);
  }
  .contact li { display: flex; align-items: center; gap: 8px; height: 21px; }
  .contact svg { width: 12px; height: 12px; fill: none; stroke: var(--ink); stroke-width: 1.6; }
  .tagline {
    position: absolute;
    left: 30px;
    top: 264px;
    font-family: "PT Serif", Georgia, serif;
    font-size: 14px;
    color: var(--brand-blue);
  }

  .brand-block--reverse {
    position: absolute;
    left: 80px;
    top: 75px;
    width: 150px;
    height: 150px;
    background: var(--paper);
  }
  .back-copy {
    position: absolute;
    left: 250px;
    top: 70px;
    width: 250px;
    text-align: center;
    font-family: "PT Serif", Georgia, serif;
    color: var(--paper);
    font-size: 23px;
    line-height: 30px;
  }
  .back-copy .site { font-style: italic; font-size: 17px; margin-top: 14px; }
</style>
</head>
<body>
  <section class="card card--front" aria-label="Card front">
    <div class="wordmark">Brinmoor<br>Legal</div>
    <div class="brand-block" aria-hidden="true"></div>
    <p class="person">Tobias Marlow, <span class="title">Attorney</span></p>
    <ul class="contact">
      <li>
        <svg viewBox="0 0 12 12"><circle cx="6" cy="6" r="5"/><path d="M4 3.5c0 2.5 1.5 4.5 4 5"/></svg>
        855-FIRM-ONE (347-6663)
      </li>
      <li>
        <svg viewBox="0 0 12 12"><rect x="1" y="2.5" width="10" height="7"/><path d="M1 2.5l5 4 5-4"/></svg>
        tobias.marlow@brinmoorlegal.com
      </li>
      <li>
        <svg viewBox="0 0 12 12"><circle cx="6" cy="6" r="5"/><path d="M1 6h10M6 1c-2.5 3-2.5 7 0 10M6 1c2.5 3 2.5 7 0 10"/></svg>
        www.brinmoorlegal.com
      </li>
    </ul>
    <p class="tagline">A Law Firm For Service Members And Veterans</p>
  </section>

  <section class="card card--back" aria-label="Card back">
    <div class="brand-block--reverse" aria-hidden="true"></div>
    <div class="back-copy">
      <p>A Law Firm<br>For Service<br>Members &amp; Veterans</p>
      <p class="site">www.brinmoorlegal.com</p>
    </div>
  </section>
</body>
</html>
```